Veldmark Supplies Business Card

Professional business card that stand out to our potential customers. Front and back with clean modern design

Industry/Entity Type

Oil and gas

Contact Information for Business Card

Name, address, website , office phone and cell number

Requirements
Must have
• Editable files for each employee

```html
<!DOCTYPE html>
<html lang="en">
<head>
<meta charset="utf-8">
<title>Veldmark Supplies Business Card</title>
<link rel="stylesheet" href="https://fonts.googleapis.com/css2?family=Roboto:wght@400;500;700;900&display=swap">
<style>
  :root {
    --canvas-bg: #2b2b2d;
    --brand-red: #e3262f;
    --brand-blue: #20a6cf;
    --gradient-mid: #7c5a78;
    --card-white: #f6f6f4;
    --ink: #3a3a3c;
    --white: #ffffff;
  }
  * { box-sizing: border-box; margin: 0; padding: 0; }
  html, body {
    width: 1200px; height: 852px; overflow: hidden;
    background: var(--canvas-bg);
    font-family: "Roboto", Arial, sans-serif;
  }
  .canvas { position: relative; width: 1200px; height: 852px; }

  .card {
    position: absolute;
    width: 540px; height: 308px;
    border-radius: 22px;
    overflow: hidden;
  }

  /* Front */
  .card-front {
    left: 80px; top: 110px;
    background: linear-gradient(35deg, var(--brand-blue) 0%, var(--gradient-mid) 52%, var(--brand-red) 100%);
    display: flex; align-items: center; justify-content: center;
  }
  .front-brand {
    display: flex; align-items: center; gap: 16px;
  }
  .front-brand .brand-mark {
    width: 34px; height: 34px; background: var(--white);
  }
  .front-brand .brand-name {
    color: var(--white);
    font-weight: 900; font-size: 30px;
    letter-spacing: 1.5px; text-transform: uppercase;
  }

  /* Back */
  .card-back {
    left: 580px; top: 434px;
    background: var(--card-white);
    padding: 42px 40px;
  }
  .back-brand { display: flex; align-items: center; gap: 12px; }
  .back-brand .brand-mark {
    width: 30px; height: 30px; border-radius: 50%; background: var(--brand-red);
  }
  .back-brand .brand-name {
    color: var(--brand-red);
    font-weight: 900; font-size: 20px;
    letter-spacing: 0.8px; text-transform: uppercase;
  }
  .person { margin-top: 30px; }
  .person-name {
    color: var(--brand-blue); font-weight: 500; font-size: 22px;
  }
  .person-title { color: var(--ink); font-size: 14px; margin-top: 2px; }
  .address { margin-top: 14px; color: var(--ink); font-size: 13px; line-height: 1.45; }
  .contacts { list-style: none; margin-top: 12px; color: var(--ink); font-size: 13px; }
  .contacts li { display: flex; align-items: center; gap: 8px; line-height: 1.55; }
  .contacts svg { width: 12px; height: 12px; fill: var(--brand-red); flex: none; }
</style>
</head>
<body>
<main class="canvas">
  <section class="card card-front" aria-label="Card front">
    <div class="front-brand">
      <span class="brand-mark"></span>
      <span class="brand-name">Veldmark Supplies</span>
    </div>
  </section>

  <section class="card card-back" aria-label="Card back">
    <div class="back-brand">
      <span class="brand-mark"></span>
      <span class="brand-name">Veldmark Supplies</span>
    </div>
    <div class="person">
      <p class="person-name">Jordan Hale Reyes</p>
      <p class="person-title">Managing Director</p>
    </div>
    <p class="address">412 St. Harlow Suite 3<br>Carrow, Tx 79750</p>
    <ul class="contacts">
      <li>
        <svg viewBox="0 0 24 24" aria-hidden="true"><path d="M6.6 10.8a15.1 15.1 0 0 0 6.6 6.6l2.2-2.2a1 1 0 0 1 1-.25 11.4 11.4 0 0 0 3.6.57 1 1 0 0 1 1 1V20a1 1 0 0 1-1 1A17 17 0 0 1 3 4a1 1 0 0 1 1-1h3.5a1 1 0 0 1 1 1c0 1.25.2 2.45.57 3.57a1 1 0 0 1-.25 1z"/></svg>
        (555)210-0148
      </li>
      <li>
        <svg viewBox="0 0 24 24" aria-hidden="true"><path d="M2 5h20v14H2z M4 7v.5l8 5 8-5V7z" fill-rule="evenodd"/></svg>
        sales@veldmarksupplies.com
      </li>
      <li>
        <svg viewBox="0 0 24 24" aria-hidden="true"><path d="M12 2a10 10 0 1 0 0 20 10 10 0 0 0 0-20zm-1 2.1V11H4.1A8 8 0 0 1 11 4.1zm2 0A8 8 0 0 1 19.9 11H13zM4.1 13H11v6.9A8 8 0 0 1 4.1 13zM13 19.9V13h6.9a8 8 0 0 1-6.9 6.9z"/></svg>
        www.veldmarksupplies.com
      </li>
    </ul>
  </section>
</main>
</body>
</html>
```